KTV Calculator

We have a calculator already created however the design seems to be very boring and bland. The calculators goal is to show graphic designers, web development firms, pr agencies, marketing firms how much revenue they can potentially make by offering a managed social media solution to their clients.

We want a great designer to make the calculator appealing to our audience.

It is an amazing offer and opportunity however I do not believe the current design does it justice

you can view and play with calculator live at http://sandbox.plorvane.com/kqtd/

Reason: We need to finalize project

```html
<!DOCTYPE html>
<html lang="en">
<head>
<meta charset="utf-8">
<title>KTV Calculator</title>
<link rel="stylesheet" href="https://fonts.googleapis.com/css2?family=Open+Sans:wght@400;600;700&display=swap">
<style>
:root{
  --backdrop:#9a5f34;
  --panel:#b3b8c3;
  --band:#333333;
  --white:#ffffff;
  --cell:#f7f7f7;
  --rule:#d5d5d5;
  --ink:#444444;
  --label:#ffffff;
  --navy-top:#30479b;
  --navy-bottom:#1f2f74;
  --orange-top:#ffa000;
  --orange-bottom:#ff5a00;
  --tick-blue:#2b3f9a;
  --tick-dark:#3a3a3a;
}
*{box-sizing:border-box;margin:0;padding:0}
html,body{width:1200px;height:912px;overflow:hidden}
body{background:var(--backdrop);font-family:"Open Sans",Arial,sans-serif;position:relative}
.calculator{position:absolute;left:75px;top:176px;width:1053px;height:499px;background:var(--panel)}
.band{position:absolute;left:60px;top:38px;width:937px;height:318px;background:var(--band);border-radius:3px;box-shadow:0 6px 10px rgba(0,0,0,.35)}
.term{position:absolute;left:70px;top:21px;width:159px;height:447px;background:var(--white);box-shadow:0 3px 4px rgba(0,0,0,.25)}
.term-title{position:absolute;left:6px;top:5px;width:148px;height:43px;background:linear-gradient(#3a3a3a,#111);border-radius:3px;color:var(--white);font-weight:600;font-size:18px;display:flex;align-items:center;justify-content:center;letter-spacing:.3px}
.term-slider{position:absolute;left:45px;top:84px}
.row-label{position:absolute;left:237px;width:200px;color:var(--label);font-weight:700;font-size:15.5px}
.row-rule{position:absolute;left:235px;width:205px;height:1px;background:#6a6a6a}
.plan{position:absolute;top:21px;width:167px;height:342px;background:var(--white);border-radius:5px;box-shadow:0 2px 4px rgba(0,0,0,.3)}
.plan-head{position:absolute;left:3px;top:3px;right:3px;height:60px;border-radius:4px;color:var(--white);font-size:21px;display:flex;align-items:center;justify-content:center}
.plan-basic .plan-head,.plan-enterprise .plan-head,.plan-basic .plan-bar,.plan-enterprise .plan-bar{background:linear-gradient(var(--navy-top),var(--navy-bottom))}
.plan-pro .plan-head,.plan-pro .plan-bar{background:linear-gradient(var(--orange-top),var(--orange-bottom))}
.plan-cell{position:absolute;left:0;right:0;background:var(--cell);border-top:1px solid var(--rule);color:var(--ink);font-size:20px;display:flex;align-items:center;justify-content:center}
.plan-cell.profit{font-weight:700;font-size:18px}
.plan-bar{position:absolute;left:3px;right:3px;top:322px;height:14px;border-radius:2px}
.stepper{position:absolute;top:50%;transform:translateY(-50%);width:36px;height:30px;background:linear-gradient(#fafafa,#dcdcdc);border-radius:4px;box-shadow:0 1px 2px rgba(0,0,0,.4);font-weight:700;font-size:22px;line-height:28px;text-align:center;color:#222}
.stepper.minus{left:-4px}
.stepper.plus{right:-4px}
.total{position:absolute;left:260px;top:388px;width:750px;height:78px;background:linear-gradient(#f3f3f3,#d9d9d9);border-radius:3px;box-shadow:0 2px 3px rgba(0,0,0,.3);color:#333;font-size:31px;display:flex;align-items:center;justify-content:center}
.total strong{font-weight:700;margin-left:9px}
</style>
</head>
<body>
<main class="calculator">
  <div class="band"></div>

  <section class="term">
    <div class="term-title">TERM (YRS)</div>
    <svg class="term-slider" width="70" height="330" viewBox="0 0 70 330">
      <rect x="8" y="0" width="46" height="335" rx="5" fill="#ececec" stroke="#dcdcdc"/>
      <g stroke-width="1">
        <line x1="0" x2="64" y1="22" y2="22" stroke="var(--tick-blue)"/>
        <line x1="0" x2="64" y1="57" y2="57" stroke="var(--tick-blue)"/>
        <line x1="0" x2="64" y1="91" y2="91" stroke="var(--tick-dark)"/>
        <line x1="0" x2="64" y1="126" y2="126" stroke="var(--tick-blue)"/>
        <line x1="0" x2="64" y1="161" y2="161" stroke="var(--tick-blue)"/>
        <line x1="0" x2="64" y1="195" y2="195" stroke="var(--tick-blue)"/>
        <line x1="0" x2="64" y1="230" y2="230" stroke="var(--tick-dark)"/>
        <line x1="0" x2="64" y1="264" y2="264" stroke="var(--tick-dark)"/>
        <line x1="0" x2="64" y1="299" y2="299" stroke="var(--tick-dark)"/>
      </g>
      <rect x="28" y="20" width="7" height="285" rx="3.5" fill="#333"/>
      <circle cx="31" cy="57" r="23" fill="var(--navy-bottom)" stroke="#fff" stroke-width="1.5"/>
      <path d="M20 62 L31 51 L42 62" fill="none" stroke="#fff" stroke-width="5" stroke-linecap="round" stroke-linejoin="round"/>
    </svg>
  </section>

  <div class="row-label" style="top:104px">Clients per month:</div>
  <div class="row-rule" style="top:144px"></div>
  <div class="row-label" style="top:172px">You pay:</div>
  <div class="row-rule" style="top:213px"></div>
  <div class="row-label" style="top:239px">Your client pays:</div>
  <div class="row-rule" style="top:282px"></div>
  <div class="row-label" style="top:309px">Monthly profit (year 8):</div>

  <section class="plan plan-basic" style="left:449px">
    <div class="plan-head">BASIC</div>
    <div class="plan-cell" style="top:74px;height:52px"><span class="stepper minus">−</span>1<span class="stepper plus">+</span></div>
    <div class="plan-cell" style="top:126px;height:67px">$197</div>
    <div class="plan-cell" style="top:193px;height:70px"><span class="stepper minus">−</span>$297<span class="stepper plus">+</span></div>
    <div class="plan-cell profit" style="top:263px;height:59px">$9,600</div>
    <div class="plan-bar"></div>
  </section>

  <section class="plan plan-pro" style="left:634px">
    <div class="plan-head">PRO</div>
    <div class="plan-cell" style="top:74px;height:52px"><span class="stepper minus">−</span>1<span class="stepper plus">+</span></div>
    <div class="plan-cell" style="top:126px;height:67px">$297</div>
    <div class="plan-cell" style="top:193px;height:70px"><span class="stepper minus">−</span>$497<span class="stepper plus">+</span></div>
    <div class="plan-cell profit" style="top:263px;height:59px">$19,200</div>
    <div class="plan-bar"></div>
  </section>

  <section class="plan plan-enterprise" style="left:816px">
    <div class="plan-head">ENTERPRISE</div>
    <div class="plan-cell" style="top:74px;height:52px"><span class="stepper minus">−</span>1<span class="stepper plus">+</span></div>
    <div class="plan-cell" style="top:126px;height:67px">$2500</div>
    <div class="plan-cell" style="top:193px;height:70px"><span class="stepper minus">−</span>$4000<span class="stepper plus">+</span></div>
    <div class="plan-cell profit" style="top:263px;height:59px">$144,000</div>
    <div class="plan-bar"></div>
  </section>

  <div class="total">Monthly profit by the end of year 8: <strong>$172,800</strong></div>
</main>
</body>
</html>
```